Web Design Project

We are looking to for a redesign for www.volketa.com. Volketa Systems is a Managed Service Provider of IT solutions based is Calgary, Alberta, Canada. We are currently expanding into the Edmonton market and would like to lauch our new site with our expansion.
The design should be sleak in style and communicate a professional vision to our clients and prospects.

Thanks,
Dale

Target Market(s)

Small to medium size businesses looking to outsource or complement their IT solutions.

Industry/Entity Type

It Professional

```html
<!DOCTYPE html>
<html lang="en">
<head>
<meta charset="utf-8">
<title>Volketa Systems — Managed IT Service Professionals</title>
<link rel="stylesheet" href="https://fonts.googleapis.com/css2?family=Source+Sans+3:wght@400;600&display=swap">
<style>
  :root {
    --page-bg: #e6e6e6;
    --hero-top: #d6d6d6;
    --hero-mid: #e4e4e4;
    --rule: #a9a9a9;
    --accent-red: #e2292d;
    --text-dark: #2b2b2b;
    --text-mid: #4a4a4a;
    --footer-light: #dedcdc;
    --footer-dark: #bdbcbc;
    --link-white: #ffffff;
    --field-top: #cfcfcf;
    --field-bottom: #a8a8a8;
    --server-dark: #1c1c1c;
    --server-edge: #3a3a3a;
  }
  * { box-sizing: border-box; margin: 0; padding: 0; }
  html, body { width: 1200px; height: 974px; overflow: hidden; }
  body {
    background: var(--page-bg);
    font-family: "Source Sans 3", "Myriad Pro", Arial, sans-serif;
    color: var(--text-dark);
    position: relative;
  }
  .abs { position: absolute; }

  /* Header */
  .brand-name { left: 98px; top: 60px; font-size: 46px; font-weight: 400; line-height: 1; color: var(--text-dark); white-space: nowrap; }
  .main-nav { top: 75px; font-size: 25px; color: var(--text-mid); }
  .main-nav a { position: absolute; color: inherit; text-decoration: none; white-space: nowrap; }
  .main-nav .is-current { color: var(--accent-red); }

  .rule { left: 8px; width: 1184px; height: 2px; background: var(--rule); }

  /* Hero */
  .hero { left: 8px; top: 157px; width: 1184px; height: 355px;
    background: linear-gradient(180deg, var(--hero-top) 0%, var(--hero-mid) 45%, var(--page-bg) 100%); }
  .hero-title { left: 70px; top: 253px; font-size: 37px; font-weight: 400; color: var(--accent-red); white-space: nowrap; }
  .hero-copy { left: 73px; top: 313px; width: 530px; font-size: 18.2px; line-height: 22px; color: var(--text-dark); }
  .hero-visual { left: 642px; top: 238px; width: 502px; height: 212px;
    background:
      linear-gradient(180deg, rgba(230,230,230,0) 0%, rgba(230,230,230,0) 72%, var(--page-bg) 100%),
      linear-gradient(90deg, var(--server-edge) 0%, var(--server-dark) 40%, var(--server-dark) 76%, #c9cdd6 80%, #b9bec9 100%);
    border-radius: 3px; }

  /* Feature columns */
  .col-divider { top: 514px; width: 2px; height: 224px;
    background: linear-gradient(180deg, transparent, #c6c6c6 30%, #c6c6c6 70%, transparent); }
  .feature-title { font-size: 27px; font-weight: 400; color: var(--accent-red); white-space: nowrap; }
  .feature-text { font-size: 20.5px; line-height: 24.5px; color: var(--text-mid); }
  .thumb { border: 2px solid #8c8c8c; }
  .thumb-security { left: 71px; top: 589px; width: 153px; height: 114px;
    background: linear-gradient(160deg, #1d3e52 0%, #2f5f74 45%, #6a2a2e 60%, #193244 100%); }
  .partner-badge { left: 459px; top: 588px; width: 107px; height: 96px; background: #ffffff; }
  .thumb-support { left: 817px; top: 587px; width: 154px; height: 117px;
    background: linear-gradient(120deg, #dfe6ef 0%, #c9d3de 30%, #a8785c 60%, #6a4330 100%); }

  /* Footer */
  .footer-shape { left: 8px; top: 740px; }
  .footer-title { left: 70px; top: 763px; font-size: 25px; font-weight: 400; color: var(--accent-red); }
  .field { left: 90px; width: 228px; height: 31px; border-radius: 10px;
    background: linear-gradient(180deg, var(--field-top), var(--field-bottom));
    color: #ffffff; font-size: 18px; line-height: 31px; padding-left: 25px; }
  .call-button { left: 383px; top: 825px; }
  .call-note { left: 447px; top: 871px; font-size: 16.5px; color: var(--text-mid); }
  .footer-nav h3 { position: absolute; font-weight: 400; font-size: 21.5px; color: var(--text-mid); white-space: nowrap; }
  .footer-nav ul { position: absolute; list-style: none; font-size: 15.5px; line-height: 22.5px; color: var(--link-white); white-space: nowrap; }
</style>
</head>
<body>

<header>
  <div class="brand-name abs">Volketa Systems</div>
  <nav class="main-nav abs">
    <a class="is-current" style="left:569px">Home</a>
    <a style="left:657px">About US</a>
    <a style="left:774px">Solutions</a>
    <a style="left:892px">Services</a>
    <a style="left:993px">Contact Us</a>
  </nav>
</header>

<div class="rule abs" style="top:154px"></div>

<section class="hero abs"></section>
<h1 class="hero-title abs">Managed IT Service Professionals</h1>
<p class="hero-copy abs">Volketa Systems employs an innovative managed service solution to provide our clients with technical expertise and superb customer service. Our goal is to ensure that our clients business requirements align with their technical needs in order to maximize their benefits</p>
<div class="hero-visual abs" role="img" aria-label="Row of black server towers with a businessman leaning on them"></div>

<div class="rule abs" style="top:512px"></div>

<section class="features">
  <div class="col-divider abs" style="left:427px"></div>
  <div class="col-divider abs" style="left:776px"></div>

  <h2 class="feature-title abs" style="left:73px;top:540px">Spotlight</h2>
  <div class="thumb thumb-security abs" role="img" aria-label="Padlocks over a digital data background"></div>
  <p class="feature-text abs" style="left:241px;top:584px;width:170px">Keep your data secure and readily available with our online backup service</p>

  <h2 class="feature-title abs" style="left:463px;top:541px">Partners</h2>
  <div class="thumb partner-badge abs"></div>
  <p class="feature-text abs" style="left:584px;top:585px;width:170px">We work with the best to bring you the best.</p>

  <h2 class="feature-title abs" style="left:820px;top:541px">Live Support</h2>
  <div class="thumb thumb-support abs" role="img" aria-label="Support agent at a computer"></div>
  <p class="feature-text abs" style="left:990px;top:584px;width:160px">Click here to access our Live support</p>
</section>

<div class="rule abs" style="top:738px"></div>

<footer>
  <svg class="footer-shape abs" width="1184" height="234" viewBox="0 0 1184 234" aria-hidden="true">
    <rect width="1184" height="234" fill="var(--footer-light)"/>
    <path d="M512,0 C590,4 612,80 642,130 C682,198 732,218 812,218 L1184,218 L1184,0 Z" fill="var(--footer-dark)"/>
  </svg>

  <h2 class="footer-title abs">Quick Connect</h2>
  <div class="field abs" style="top:802px">Name:</div>
  <div class="field abs" style="top:842px">E-mail:</div>
  <div class="field abs" style="top:883px">Comment:</div>

  <svg class="call-button abs" width="184" height="56" viewBox="0 0 184 56" aria-label="Connect Now">
    <defs>
      <linearGradient id="btn" x1="0" y1="0" x2="0" y2="1">
        <stop offset="0" stop-color="#6a6a6a"/><stop offset="1" stop-color="#2e2e2e"/>
      </linearGradient>
    </defs>
    <rect x="30" y="13" width="152" height="29" rx="10" fill="url(#btn)"/>
    <circle cx="27" cy="28" r="27" fill="url(#btn)"/>
    <circle cx="27" cy="28" r="23" fill="none" stroke="#8a8a8a" stroke-width="1.5"/>
    <path d="M19,16 c3,-2 5,-1 6,2 l1,4 c0,2 -2,3 -3,4 c1,4 4,7 7,9 c1,-1 2,-3 4,-2 l4,2 c2,1 2,4 0,6 c-3,2 -7,2 -11,-1 c-6,-5 -10,-11 -11,-17 c0,-3 1,-6 3,-7 z" fill="#ffffff"/>
    <text x="59" y="33" font-family="'Source Sans 3', Arial, sans-serif" font-size="19.5" fill="#ffffff">Connect Now</text>
  </svg>
  <p class="call-note abs">Free number</p>

  <nav class="footer-nav">
    <h3 style="left:688px;top:767px">About US</h3>
    <ul style="left:703px;top:798px"><li>Company</li><li>Mission</li><li>History</li><li>Community</li></ul>
    <h3 style="left:808px;top:767px">Solutions</h3>
    <ul style="left:822px;top:800px"><li>Managed Services</li><li>Virtualization</li><li>Online Backup</li><li>Development</li><li>Storage</li></ul>
    <h3 style="left:953px;top:767px">Services</h3>
    <ul style="left:966px;top:798px"><li>Planning</li><li>Delivery</li><li>Operation</li><li>Management</li></ul>
    <h3 style="left:1059px;top:767px">Contact Us</h3>
    <ul style="left:1075px;top:796px"><li>Careers</li></ul>
  </nav>
</footer>

</body>
</html>
```